Fresh, modern, fun business card for pediatric dental practice

Need a business card for fresh, modern, fun pediatric dental practice

Clean look that matches our website's font and colors

We prefer the look of curved corners on business cards

Target Market(s)

parents (mothers) of young children, professionals, mid-high class

Industry/Entity Type

Dental

Contact Information for Business Card

Maplebrook Pediatric Dentistry
482 Quarry Lane
Suite 517
Alderton, PA 17990
717.555.0193
www.maplebrookkidsdental.example

Mei-Ran Tsai, DMD
Corinne Walbeck, DMD
(we are working on our email address, but we would like that on the card as well)

Font styles to use
Sans Serif

Requirements
Must have
• All info; we would also like to make cards for individual staff members
• colors from our website and color palatte, attatched
• use same font and design as website for branding
Nice to have
• clean, simple card that has a pop of color
• we would like to see a few designs with our tag line "where smiles get brighter"
• we are not sure if we want to have it on there or not
• we would like to see a few designs incorporating the ribbon graphic on our website where the word WELCOME is

```html
<!DOCTYPE html>
<html lang="en">
<head>
<meta charset="utf-8">
<title>Maplebrook Pediatric Dentistry – Business Card</title>
<link rel="stylesheet" href="https://fonts.googleapis.com/css2?family=Open+Sans:wght@400;600;700&display=swap">
<style>
  :root {
    --page: #3a3532;
    --card: #0d0d0d;
    --ink-white: #f4f4f4;
    --ink-soft: #d9d9d9;
    --pink: #d1359b;
    --sun: #f6b428;
    --rule: #3b3b3b;
  }
  * { box-sizing: border-box; margin: 0; padding: 0; }
  html, body {
    width: 1200px; height: 900px; overflow: hidden;
    background: var(--page);
    font-family: "Open Sans", Arial, sans-serif;
  }
  .stage {
    position: relative; width: 1200px; height: 900px;
    display: flex; align-items: center; justify-content: center; gap: 44px;
  }
  .card {
    position: relative; width: 520px; height: 297px;
    background: var(--card); border-radius: 18px;
    box-shadow: 0 10px 28px rgba(0,0,0,.45);
    overflow: hidden;
  }

  /* front */
  .wordmark { position: absolute; left: 150px; top: 36px; }
  .wordmark__name {
    display: block; color: var(--ink-white);
    font-weight: 700; font-size: 52px; line-height: 1; letter-spacing: 1px;
  }
  .wordmark__line {
    display: block; color: var(--pink);
    font-weight: 400; font-size: 24px; line-height: 1.25; letter-spacing: 2.5px;
  }

  .doctors {
    position: absolute; right: 272px; top: 180px;
    text-align: right; color: var(--ink-soft);
  }
  .doctor__name { color: var(--pink); font-weight: 700; font-size: 15px; line-height: 1.15; }
  .doctor__email { font-size: 12px; line-height: 1.3; }

  .divider {
    position: absolute; left: 258px; top: 160px; width: 1px; height: 110px;
    background: var(--rule);
  }

  .contact {
    position: absolute; left: 272px; top: 165px;
    color: var(--ink-soft); font-size: 11.5px; line-height: 1.45;
  }
  .contact__row { display: flex; align-items: center; gap: 6px; }
  .contact__row svg { width: 9px; height: 9px; flex: none; }
  .contact__address { margin-top: 8px; }

  /* back */
  .card--back .brand {
    position: absolute; left: 0; right: 0; top: 74px;
    display: flex; flex-direction: column; align-items: center;
  }
  .brand__dot { width: 46px; height: 46px; border-radius: 50%; background: var(--sun); margin-bottom: 14px; }
  .brand__name { color: var(--sun); font-weight: 700; font-size: 54px; line-height: 1; letter-spacing: 1px; }
  .brand__line { color: var(--pink); font-weight: 400; font-size: 23px; letter-spacing: 2.5px; margin-top: 4px; }
</style>
</head>
<body>
<main class="stage">

  <section class="card card--front" aria-label="Card front">
    <div class="wordmark">
      <span class="wordmark__name">maplebrook</span>
      <span class="wordmark__line">pediatric dentistry</span>
    </div>

    <div class="doctors">
      <p class="doctor__name">Mei-Ran Tsai, DMD</p>
      <p class="doctor__email">mei-ran@maplebrookkidsdental.example</p>
      <p class="doctor__name">Corinne Walbeck, DMD</p>
      <p class="doctor__email">mei-ran@maplebrookkidsdental.example</p>
    </div>

    <div class="divider"></div>

    <div class="contact">
      <p class="contact__row">
        <svg viewBox="0 0 10 10" aria-hidden="true"><rect x="2.5" y="0.5" width="5" height="9" rx="1" fill="none" stroke="var(--pink)" stroke-width="1.2"/></svg>
        717.555.0193
      </p>
      <p class="contact__row">
        <svg viewBox="0 0 10 10" aria-hidden="true"><circle cx="5" cy="5" r="4.5" fill="var(--pink)"/></svg>
        www.maplebrookkidsdental.example
      </p>
      <p class="contact__address">Maplebrook Pediatric Dentistry<br>482 Quarry Lane Suite 517<br>Alderton, PA 17990</p>
    </div>
  </section>

  <section class="card card--back" aria-label="Card back">
    <div class="brand">
      <span class="brand__dot"></span>
      <span class="brand__name">maplebrook</span>
      <span class="brand__line">pediatric dentistry</span>
    </div>
  </section>

</main>
</body>
</html>
```